Velmora Freightway Solutions Business cards

Would like a very unique design catchy but professional for business cards. Please use log provided.Marlon WellsCeo and Founder TransCon Logistix Solutions1-888-913-3225mwells@tlsolutionsus.comwww.tlsolutionsus.com

```html
<!DOCTYPE html>
<html lang="en">
<head>
<meta charset="utf-8">
<title>Velmora Freightway Solutions – Business Card</title>
<link href="https://fonts.googleapis.com/css2?family=Josefin+Sans:wght@700&family=Lato:wght@400&display=swap" rel="stylesheet">
<style>
  :root {
    --page: #ececec;
    --card-white: #fbfbfb;
    --brand-blue: #1673c0;
    --brand-red: #e52530;
    --ink-white: #ffffff;
  }
  * { box-sizing: border-box; margin: 0; padding: 0; }
  html, body { width: 1200px; height: 900px; overflow: hidden; background: var(--page); }
  .card {
    position: absolute; left: 100px; top: 140px; width: 1000px; height: 620px;
    background: var(--card-white); overflow: hidden;
    box-shadow: 0 10px 30px rgba(0,0,0,0.15);
  }
  .card__brand {
    position: absolute; left: 0; top: 0; width: 100%; height: 375px;
    display: flex; align-items: center; justify-content: center; gap: 18px;
  }
  .brand__mark { width: 34px; height: 34px; background: var(--brand-red); }
  .brand__name {
    font-family: 'Josefin Sans', sans-serif; font-weight: 700; font-size: 46px;
    color: var(--brand-blue); letter-spacing: 1px; text-transform: uppercase;
    padding-top: 6px;
  }
  .card__rule { position: absolute; left: 0; top: 375px; width: 100%; height: 9px; background: var(--brand-red); }
  .card__contact-band {
    position: absolute; left: 0; top: 384px; width: 100%; height: 236px; background: var(--brand-blue);
    color: var(--ink-white);
  }
  .holder { position: absolute; right: 535px; top: 82px; text-align: right; }
  .holder__name { font-family: 'Josefin Sans', sans-serif; font-weight: 700; font-size: 33px; letter-spacing: 1px; text-transform: uppercase; }
  .holder__title { font-family: 'Lato', sans-serif; font-size: 26px; margin-top: 2px; }
  .divider { position: absolute; left: 500px; top: 72px; width: 2px; height: 98px; background: var(--ink-white); opacity: 0.85; }
  .contact-list { position: absolute; left: 522px; top: 66px; list-style: none; font-family: 'Lato', sans-serif; font-size: 27px; }
  .contact-list li { display: flex; align-items: center; gap: 10px; height: 37px; }
  .contact-list svg { width: 20px; height: 20px; fill: var(--ink-white); flex: none; }
</style>
</head>
<body>
  <div class="card">
    <div class="card__brand">
      <span class="brand__mark"></span>
      <span class="brand__name">Velmora Freightway Solutions</span>
    </div>
    <div class="card__rule"></div>
    <div class="card__contact-band">
      <div class="holder">
        <div class="holder__name">Lucas Brenner</div>
        <div class="holder__title">CEO and Founder</div>
      </div>
      <div class="divider"></div>
      <ul class="contact-list">
        <li>
          <svg viewBox="0 0 20 20" aria-hidden="true"><path d="M2 7c0-3 3-4 8-4s8 1 8 4v1h-4V6H6v2H2z"/><path d="M4 9h12l2 8H2z"/><circle cx="10" cy="13" r="2" fill="#1673c0"/></svg>
          1-888-470-6158
        </li>
        <li>
          <svg viewBox="0 0 20 20" aria-hidden="true"><rect x="1" y="4" width="18" height="12"/><path d="M1 4l9 7 9-7" fill="none" stroke="#1673c0" stroke-width="1.6"/></svg>
          dpike@vfwayroutes.com
        </li>
        <li>
          <svg viewBox="0 0 20 20" aria-hidden="true"><circle cx="10" cy="10" r="9"/><path d="M5 6c2 0 3 2 2 4s2 3 1 5M12 3c0 2 2 3 4 3" fill="none" stroke="#1673c0" stroke-width="1.6"/></svg>
          www.vfwayroutes.com
        </li>
      </ul>
    </div>
  </div>
</body>
</html>
```